Dynamic Business Card for Sports Supplements Company

Hi! I'm looking for an awesome business card to match my existing sports supplement company. I have uploaded my current company logo and screenshot of the front page of my website.

I would like to have something dynamic and interesting and utilize the colors in the website - the reds and purples

The business card should be double sided and focus on a unique eye-catching design on the back and include all the relevant company info.

Most importantly, it should say somewhere: "Sign up on our website for a coupon code."

Target Market(s)

Mostly for women gym goers but it shouldn't be too feminine. It should be in keeping with the website design. It should flow and clearly be connected to it

Industry/Entity Type

Business

Contact Information for Business Card

Lorraine K. Vestal
CEO
LVestal@Quorvanexco.com
www.quorvanexco.com
555.417.3820
P.O. Box 47315
Alder Ridge, Vermont 00000

Sign up on our website for a coupon code

Font styles to use
Serif
Sans Serif
Other font styles liked:
• Novecento font family and "Quorvanex" is in AR Destine font

Requirements
Must have
• One side should be a bold Quorvanex logo design. Even just the symbol itself may be o.k. (see attached file)

```html
<!DOCTYPE html>
<html lang="en">
<head>
<meta charset="utf-8">
<title>Quorvanex Business Card</title>
<link href="https://fonts.googleapis.com/css2?family=Montserrat:wght@400;500;700&display=swap" rel="stylesheet">
<style>
  :root {
    --backdrop: #3b3b3d;
    --purple: #332b5e;
    --red: #e3202a;
    --ink: #111111;
    --grey: #6d6d6d;
    --paper: #ffffff;
  }
  html, body {
    margin: 0;
    padding: 0;
    width: 1200px;
    height: 855px;
    overflow: hidden;
    background: var(--backdrop);
    font-family: "Montserrat", sans-serif;
  }
  .stage { position: relative; width: 1200px; height: 855px; }
  .card {
    position: absolute;
    left: 354px;
    width: 493px;
    box-shadow: 0 4px 10px rgba(0,0,0,0.35);
  }
  .card-front {
    top: 137px;
    height: 281px;
    background: var(--purple);
    color: var(--paper);
  }
  .front-brand {
    position: absolute;
    left: 0; right: 0;
    top: 122px;
    display: flex;
    align-items: center;
    justify-content: center;
    gap: 12px;
  }
  .brand-dot {
    width: 22px; height: 22px;
    border-radius: 50%;
    background: var(--red);
  }
  .front-name {
    font-size: 30px;
    font-weight: 700;
    letter-spacing: 1px;
    text-transform: uppercase;
    color: var(--paper);
  }
  .coupon-line {
    position: absolute;
    left: 0; right: 0;
    top: 239px;
    margin: 0;
    text-align: center;
    font-size: 13px;
    font-weight: 400;
  }
  .card-back {
    top: 430px;
    height: 288px;
    background: var(--paper);
  }
  .edge-stripe { position: absolute; left: 0; top: 0; }
  .back-brand {
    position: absolute;
    left: 297px;
    top: 100px;
    width: 176px;
    text-align: center;
  }
  .back-name {
    font-size: 22px;
    font-weight: 700;
    letter-spacing: 1px;
    text-transform: uppercase;
    color: var(--ink);
    line-height: 1;
  }
  .tagline {
    font-size: 8.5px;
    letter-spacing: 0.6px;
    color: var(--ink);
    margin-top: 3px;
    white-space: nowrap;
  }
  .person {
    position: absolute;
    left: 26px;
    top: 119px;
  }
  .person-name { font-size: 18px; font-weight: 500; color: var(--ink); line-height: 22px; }
  .person-role { font-size: 13px; color: var(--grey); line-height: 17px; }
  .address { margin-top: 12px; font-size: 13px; color: var(--grey); line-height: 17px; }
  .contacts { margin-top: 12px; font-size: 13px; color: var(--grey); line-height: 17px; }
  .contact-row { display: flex; align-items: center; gap: 5px; }
  .contact-row svg { width: 11px; height: 11px; flex: none; }
</style>
</head>
<body>
<div class="stage">
  <section class="card card-front">
    <div class="front-brand">
      <span class="brand-dot"></span>
      <span class="front-name">Quorvanex</span>
    </div>
    <p class="coupon-line">Sign up on our website for a coupon code</p>
  </section>

  <section class="card card-back">
    <svg class="edge-stripe" width="12" height="288" viewBox="0 0 12 288">
      <polygon points="0,0 10,0 10,130 0,120" fill="var(--red)"/>
      <polygon points="0,124 10,134 10,288 0,288" fill="var(--ink)"/>
    </svg>

    <div class="back-brand">
      <div class="back-name">Quorvanex</div>
      <div class="tagline">STRONGER EVERY SINGLE DAY</div>
    </div>

    <div class="person">
      <div class="person-name">Lorraine K. Vestal</div>
      <div class="person-role">CEO</div>
      <div class="address">
        <div>P.O. Box 47315</div>
        <div>Alder Ridge, Vermont 00000</div>
      </div>
      <div class="contacts">
        <div class="contact-row">
          <svg viewBox="0 0 12 12"><path d="M2 11 C1 7 3 3 7 1.5 L9 1 L10.5 3 L8.5 4.5 C6 5.5 4.5 7.5 4.5 10 L2 11 Z" fill="var(--red)"/></svg>
          <span>555.417.3820</span>
        </div>
        <div class="contact-row">
          <svg viewBox="0 0 12 12"><rect x="0.5" y="2.5" width="11" height="7.5" fill="var(--red)"/><path d="M0.5 2.5 L6 7 L11.5 2.5" stroke="#fff" stroke-width="1" fill="none"/></svg>
          <span>LVestal@Quorvanexco.com</span>
        </div>
        <div class="contact-row">
          <svg viewBox="0 0 12 12" fill="none" stroke="var(--red)" stroke-width="1"><circle cx="6" cy="6" r="5"/><ellipse cx="6" cy="6" rx="2.2" ry="5"/><path d="M1 6 H11 M2 3.5 H10 M2 8.5 H10"/></svg>
          <span>www.quorvanexco.com</span>
        </div>
      </div>
    </div>
  </section>
</div>
</body>
</html>
```